Flyer-Design für  junges, dynamisches Unternehmen, spezialisiert auf innovative Trainingskonzepte
Flyer-Design für junges, dynamisches Unternehmen, spezialisiert auf innovative Trainingskonzepte
volTEK
Sehr kreative und ideenreiche Umsetzungen. Alle Wünsche sind sehr sorgfältig, gewissenhaft und mit absoluter Schnelligkeit erfolgt.
Zielgruppe
Als junges dynamisches Unternehmen ist volTEK spezialisiert auf innovative Trainingskonzepte. Wir sind
ein international anerkanntes Trainingscenter der Northfield Rescue Council und bieten Notfalltrainings,
Erste-Hilfe-Kurse sowie hochwertige Simulationstrainings fur Rettungsdienste und Krankenhäuser an. In
unseren CRM- Simulationstrainings coachen wir Notfallteams in den Bereichen Skills, Human Factor und
Kommunikation. Hierbei kommen Full-Scale-Simulatoren und Schauspielpatienten zum Einsatz, die eine
realitätsnahe und lebensechte Trainingssituation präsentieren.
Aufgabenstellung
Wir suchen zur Vermarktung unserer Kurse eine graphische Übersicht, aus der die Qualitätsmerkmale von volTEK, eine Zielgruppen definition sowie eine detailierte Aufarbeitung der Kursinhalte in den Verschiedenen Kursformaten hervorgeht und unsere zukünftigen Kunden von uns überzeugt.
Großer Fokus dieses Projektes, ist es die Innenseite des Flyers zu gestalten, die ein geschlossenes Gesamtbild aufweisen soll. Deckblatt und Rückseite sind nebensächlich, hier freuen wir uns über neue Ideen, aber das Fokus ist die Gestaltung der Innenseite.

```html
<!DOCTYPE html>
<html lang="de">
<head>
<meta charset="utf-8">
<title>Kursdetails &amp; Preise – volTEK</title>
<link href="https://fonts.googleapis.com/css2?family=Exo+2:ital,wght@1,700&family=Fjalla+One&family=Roboto+Condensed:wght@400&family=Source+Sans+3:ital,wght@0,400;1,400;1,600&display=swap" rel="stylesheet">
<style>
  :root{
    --red:#d81e25;
    --red-dark:#a3121b;
    --grey:#4a4a4a;
    --line:#555;
    --text:#333;
    --panel:#e6e6e8;
    --white:#fff;
  }
  *{box-sizing:border-box;margin:0;padding:0}
  html,body{width:1200px;height:849px;overflow:hidden;background:var(--white)}
  .sheet{position:relative;width:1200px;height:849px;overflow:hidden;font-family:"Source Sans 3",sans-serif;color:var(--text)}
  .deco{position:absolute;left:0;top:0}
  .page-title{position:absolute;left:145px;top:12px;font-family:"Exo 2",sans-serif;font-style:italic;font-weight:700;font-size:28px;color:var(--white)}
  .tier-head{position:absolute;top:103px;width:186px;height:43px;background:linear-gradient(90deg,var(--red-dark),var(--red));
    box-shadow:2px 3px 6px rgba(0,0,0,.3);color:var(--white);font-family:"Fjalla One",sans-serif;font-size:17px;
    display:flex;align-items:center;justify-content:center;letter-spacing:.2px}
  .tier-price{position:absolute;top:158px;font-family:"Fjalla One",sans-serif;font-size:11.5px;color:#3a3a3a;white-space:nowrap}
  .topic{position:absolute;width:186px;border:1.3px solid var(--red);background:var(--white);box-shadow:2px 3px 5px rgba(0,0,0,.18);
    display:flex;align-items:center;padding:0 11px;font-family:"Roboto Condensed",sans-serif;font-size:8.4px;line-height:12px;color:#3a3a3a}
  .footnote{position:absolute;left:393px;top:551px;font-style:italic;font-size:14px;color:#444}
  .benefits{position:absolute;left:870px;top:447px;width:320px}
  .benefits h2{font-style:italic;font-weight:600;font-size:12px;color:var(--red);margin-bottom:9px}
  .benefits li{list-style:none;font-size:9.6px;line-height:15.4px;color:#444}
  .benefits li::before{content:"- ";}
  .info-panel{position:absolute;left:0;top:621px;width:1200px;height:180px;background:var(--panel)}
  .course-text{position:absolute;left:36px;top:640px;width:510px}
  .course-text p{font-size:9.6px;line-height:13.2px;color:#444;margin-bottom:13px}
  .course-text strong{font-style:italic;font-weight:600;font-size:12px;color:var(--red)}
  .photo{position:absolute;top:621px;height:173px}
  .photo-1{left:599px;width:201px;background:linear-gradient(135deg,#2a2d36,#6a6060 60%,#c9463c)}
  .photo-2{left:803px;width:200px;background:linear-gradient(160deg,#5a5652,#30323a 45%,#b84a3c)}
  .photo-3{left:1007px;width:193px;background:linear-gradient(120deg,#3a3230,#d9322c 55%,#8a7e78)}
  .site-url{position:absolute;left:1005px;top:816px;font-family:"Exo 2",sans-serif;font-style:italic;font-weight:700;font-size:18px;color:var(--white)}
</style>
</head>
<body>
<div class="sheet">
  <svg class="deco" width="1200" height="849" viewBox="0 0 1200 849" aria-hidden="true">
    <defs>
      <linearGradient id="band" x1="0" x2="1"><stop offset="0" stop-color="#a3121b"/><stop offset="1" stop-color="#e52229"/></linearGradient>
    </defs>
    <!-- header band -->
    <path d="M0 80 Q400 55 780 52 L0 64 Z" fill="#4a4a4a"/>
    <path d="M0 0 H1160 Q900 40 500 58 Q200 62 0 55 Z" fill="url(#band)"/>
    <!-- footer band -->
    <path d="M280 812 Q700 792 1200 790 V800 Q700 805 280 812 Z" fill="#4a4a4a"/>
    <path d="M50 849 Q500 802 1200 800 V849 Z" fill="url(#band)"/>
    <!-- connector lines -->
    <g stroke="var(--line)" stroke-width="1" fill="none">
      <path d="M130 125 H117 V521 H130"/>
      <path d="M117 204 H130 M117 271 H130 M117 331 H130 M117 394 H130 M117 458 H130"/>
      <path d="M372 125 H360 V564 H238"/>
      <path d="M360 204 H372 M360 271 H372 M360 331 H372 M360 394 H372 M360 458 H372"/>
      <path d="M614 125 H600 V577 H238"/>
      <path d="M600 204 H614 M600 271 H614 M600 363 H614"/>
      <path d="M857 125 H843 V589 H238"/>
      <path d="M843 204 H857 M843 271 H857 M843 363 H857"/>
      <path d="M238 226 V245 M238 290 V308 M238 354 V372 M238 417 V435 M238 480 V499 M238 544 V589"/>
      <path d="M478 226 V245 M478 290 V308 M478 354 V372 M478 417 V435 M478 480 V589"/>
      <path d="M722 226 V245 M722 290 V308 M722 417 V589"/>
    </g>
  </svg>

  <h1 class="page-title">Kursdetails &amp; Preise</h1>

  <div class="tier-head" style="left:145px">Light</div>
  <div class="tier-head" style="left:387px">Basic*</div>
  <div class="tier-head" style="left:629px">Premium*</div>
  <div class="tier-head" style="left:872px">PremiumPLUS*</div>

  <div class="tier-price" style="left:145px">2Std. | BLS | 1 Instruktor: 123,-</div>
  <div class="tier-price" style="left:387px">3 Std. | 1 Instruktor | BLS + CRM: 234,-</div>
  <div class="tier-price" style="left:628px">4 Std. | 1 Instruktor | BLS+CRM: 456,-</div>
  <div class="tier-price" style="left:872px">Ab 4 Std. | 2 Intruktoren | BLS+ALS+CRM: 7890,-</div>

  <!-- Light -->
  <div class="topic" style="left:145px;top:181px;height:45px">Vorstellungen und Erläuterung des<br>Basic-Life-Support für med. Fachpersonal</div>
  <div class="topic" style="left:145px;top:245px;height:45px">Auffinden eines bewusstlosen Patienten</div>
  <div class="topic" style="left:145px;top:308px;height:46px">High-Performance-Reanimation, 5 Kriterien für<br>eine perfekte Herz-Druck-Massage</div>
  <div class="topic" style="left:145px;top:372px;height:45px">Vorstellung Beutel-Masken-Beatmung, LTTubus<br>und Pocketmaske</div>
  <div class="topic" style="left:145px;top:435px;height:45px">Vorstellung und Anwendung AED (Defi)</div>
  <div class="topic" style="left:145px;top:499px;height:45px">Trainingsszenarien zum Ablauf einer Reanimation</div>

  <!-- Basic -->
  <div class="topic" style="left:387px;top:181px;height:45px">Übungen zur Beatmung für jeden Teilnehmer</div>
  <div class="topic" style="left:387px;top:245px;height:45px">Übungen mit dem AED für jeden Teilnehmer</div>
  <div class="topic" style="left:387px;top:308px;height:46px">Elektronische Auswertung der<br>Reanimationsergebnisse</div>
  <div class="topic" style="left:387px;top:372px;height:45px">Training zur Teamkoordination und<br>Teamkommunikation</div>
  <div class="topic" style="left:387px;top:435px;height:45px">Fallbeispiele zur Reanimation mit Feedback zur<br>Aufgabenbewältigung und Kommunikation</div>

  <!-- Premium -->
  <div class="topic" style="left:629px;top:181px;height:45px">Überprüfung und auf Wunsch Anpassung der<br>internen Abläufe der Rettungskette (QMNotfallplan)</div>
  <div class="topic" style="left:629px;top:245px;height:45px">Fallbeispieltraining mit echtem Patienten<br>(Schauspieler)</div>
  <div class="topic" style="left:629px;top:308px;height:109px">Fallbeispiel zu ausgewählten und passenden<br>Themen wie Asthma, Anaphylaxie,<br>Krampfanfall, Bolusgeschehen, Herzinfarkt,<br>etc. die Auswahl erfolgt Anhand der<br>Fachrichtung/Praxisschwerpunkt</div>

  <!-- PremiumPLUS -->
  <div class="topic" style="left:872px;top:181px;height:45px">ABCDE-Schema zur Ersteinschätzung von<br>kritisch kranken Patienten</div>
  <div class="topic" style="left:872px;top:245px;height:45px">FORDEC-Training zur Entscheidungsfindung</div>
  <div class="topic" style="left:872px;top:308px;height:109px">Fallbeispiele zu lebensbedrohlichen<br>Situationen mit einem High-Tech-Simulator<br>u.a. mit Sprachfunktion, realistischen<br>Atembewegungen mit Atemgeräuschen,<br>Zyanose, tastebaren Pulsen und der<br>Durchführung von Maßnahmen (z.B.:<br>Entlastungspunktion, Infusiontherapie, etc.)</div>

  <p class="footnote">*Beinhaltet immer die vorrausgehenden Kurspackete</p>

  <section class="benefits">
    <h2>Was sind unsere Vorteile/Was zeichnet volTEK aus?</h2>
    <ul>
      <li>Zertifizierte und anerkannte Kurskonzepte</li>
      <li>Angenehme Lernatmosphäre mit emphatischen Instruktoren</li>
      <li>Realistische Aus- und Fortbildung mit Schauspielpatienten</li>
      <li>Modernstes Material, Technik und Simulatoren</li>
      <li>Alle Dozenten mit langjähriger Erfahrung in der Notfallmedizin</li>
      <li>Praxisorientierte und individuelle Kursgestaltung</li>
      <li>Durchführung der Schulungen bei unseren Kunden Inhouse vor Ort</li>
      <li>Förderung der Teamarbeit durch Crew Ressource Management</li>
    </ul>
  </section>

  <div class="info-panel"></div>
  <div class="course-text">
    <p><strong>Notfalltraining Light -</strong> Lernen Sie in diesem Skilltraining die Reanimation und beherrschen Sie die Herzdruckmassage. Außerdem besprechen wir die Intubation und die Defibrillation mit einem AED.</p>
    <p><strong>Notfalltraining Basic -</strong> Interaktives Team-Training: Üben Sie die wichtigsten Handgriffe und lernen Sie Ihre eigene Notfallausrüstung kennen. Das medizinische Know-How wird durch zusätzliche Themen wie Teamwork und Kommunikation erweitert.</p>
    <p><strong>Notfalltraining Premium -</strong> Weg mit der Puppe! Wir bringen unseren Schauspielpatienten mit zu Ihnen! Wir trainieren dynamische Notfälle und gemeinsam mit Ihnen analysieren und optimieren wir Ihr Notfallmanagement in Ihrer Praxis. Mit diesem Training schaffen Sie eine hohe Zufriedenheit mit Ihren Mitarbeitern und sind perfekt auf den nächsten Notfall vorbereitet. Auf Wunsch bieten wir Ihnen eine kostenlose Beratung und Verwaltung Ihrer Notfallausrüstung an.</p>
  </div>

  <div class="photo photo-1" role="img" aria-label="Foto: Herzdruckmassage an einer Reanimationspuppe"></div>
  <div class="photo photo-2" role="img" aria-label="Foto: Notfallteam versorgt einen Simulator am Boden"></div>
  <div class="photo photo-3" role="img" aria-label="Foto: Rettungskräfte beatmen einen Schauspielpatienten"></div>

  <div class="site-url">www.volTEK.de</div>
</div>
</body>
</html>
```